Freelance business trainer needs a new business card

My business is called Brontlearn. I provide training in the workplace on management, coaching and mentoring, and customer service topics for a variety of businesses, colleges and private training providers, and teach on management programs. I need a professional but eye catching business card. Business colours grey and orange. My name Marion Tadwick; Tel 07382 415067; email mtadwick@brontlearn.co.uk; website www.brontlearn.co.uk.
Happy to have some sort of logo on front and details on back or all on one side
Target Market(s)
SME businesses and colleges - workshops i run are for adults in the workplace
Industry/Entity Type
Training
Look and feel

```html
<!DOCTYPE html>
<html lang="en">
<head>
<meta charset="utf-8">
<title>Brontlearn – Business Card</title>
<link rel="stylesheet" href="https://fonts.googleapis.com/css2?family=Open+Sans:wght@400;600;700&display=swap">
<style>
  :root {
    --backdrop: #9b9b9b;
    --orange: #f69322;
    --charcoal: #414141;
    --charcoal-edge: #333333;
    --white: #ffffff;
    --rule: rgba(255, 255, 255, 0.35);
  }
  * { box-sizing: border-box; margin: 0; padding: 0; }
  html, body {
    width: 1200px;
    height: 750px;
    overflow: hidden;
  }
  body {
    position: relative;
    background: var(--backdrop);
    font-family: "Open Sans", Arial, sans-serif;
  }
  .card {
    position: absolute;
    top: 215px;
    width: 496px;
    height: 287px;
    border-radius: 20px;
  }
  .card-front {
    left: 90px;
    background: var(--orange);
    border: 4px solid var(--charcoal-edge);
  }
  .card-back {
    left: 618px;
    background: var(--charcoal);
    border: 3px solid var(--orange);
  }

  /* Front */
  .front-brand {
    position: absolute;
    left: 0;
    right: 0;
    top: 98px;
    display: flex;
    justify-content: center;
    align-items: center;
    gap: 10px;
  }
  .brand-square {
    width: 14px;
    height: 14px;
    background: var(--charcoal);
  }
  .front-brand .brand-name {
    font-weight: 700;
    font-size: 44px;
    color: var(--charcoal);
    letter-spacing: 0.5px;
  }
  .front-web {
    position: absolute;
    left: 0;
    right: 0;
    top: 202px;
    display: flex;
    justify-content: center;
    align-items: center;
    gap: 8px;
    color: var(--white);
    font-size: 14px;
    font-weight: 600;
    letter-spacing: 0.3px;
  }
  .front-web .web-line {
    width: 44px;
    height: 1px;
    background: rgba(255, 255, 255, 0.6);
  }

  /* Back */
  .back-brand {
    position: absolute;
    left: 28px;
    top: 118px;
    font-weight: 700;
    font-size: 32px;
    color: var(--orange);
    letter-spacing: 0.3px;
  }
  .back-divider {
    position: absolute;
    left: 227px;
    top: 70px;
    width: 1px;
    height: 146px;
    background: linear-gradient(to bottom, transparent, var(--rule), transparent);
  }
  .contact {
    position: absolute;
    left: 265px;
    top: 84px;
    color: var(--white);
  }
  .contact-name {
    font-weight: 700;
    font-size: 14.5px;
    line-height: 20px;
  }
  .contact-role {
    font-size: 14px;
    line-height: 22px;
    margin-bottom: 16px;
  }
  .contact-list { list-style: none; }
  .contact-list li {
    display: flex;
    align-items: center;
    gap: 5px;
    font-size: 14px;
    line-height: 22px;
  }
  .contact-icon {
    width: 13px;
    height: 13px;
    flex: none;
  }
</style>
</head>
<body>
  <section class="card card-front" aria-label="Card front">
    <div class="front-brand">
      <span class="brand-square"></span>
      <span class="brand-name">Brontlearn</span>
    </div>
    <div class="front-web">
      <span class="web-line"></span>
      <span>www.brontlearn.co.uk</span>
      <span class="web-line"></span>
    </div>
  </section>

  <section class="card card-back" aria-label="Card back">
    <div class="back-brand">Brontlearn</div>
    <div class="back-divider"></div>
    <div class="contact">
      <p class="contact-name">Marion Tadwick</p>
      <p class="contact-role">Owner</p>
      <ul class="contact-list">
        <li>
          <svg class="contact-icon" viewBox="0 0 16 16" aria-hidden="true">
            <path fill="#f69322" d="M2 5c0-2 2-3 6-3s6 1 6 3v1h-3.5V4.5h-5V6H2zM4 7h8l2 6H2z"/>
            <circle cx="8" cy="10" r="1.6" fill="#414141"/>
          </svg>
          <span>07382 415067</span>
        </li>
        <li>
          <svg class="contact-icon" viewBox="0 0 16 16" aria-hidden="true">
            <rect x="1" y="3" width="14" height="10" fill="#f69322"/>
            <path d="M1 3l7 6 7-6" fill="none" stroke="#414141" stroke-width="1.3"/>
          </svg>
          <span>mtadwick@brontlearn.co.uk</span>
        </li>
        <li>
          <svg class="contact-icon" viewBox="0 0 16 16" aria-hidden="true">
            <circle cx="8" cy="8" r="7" fill="#f69322"/>
            <g fill="none" stroke="#414141" stroke-width="1">
              <ellipse cx="8" cy="8" rx="3" ry="7"/>
              <path d="M1 8h14M2.5 4.5h11M2.5 11.5h11"/>
            </g>
          </svg>
          <span>www.brontlearn.co.uk.</span>
        </li>
      </ul>
    </div>
  </section>
</body>
</html>
```